Kelvaro.ch is looking for business card letterhead and envelope C5 with WOW effect

We need a strong business card for our company Kelvaro.ch, logo is available. You want a black or dark background on which the logo Stark r% 26 # 252; appears. Letterhead and envelope in C5 format should be in a similar design, but does not have to be We need a strong business card for our company Kelvaro.ch, logo is available. A black or dark background is desired, on which the logo Stark comes across. The letterhead and the envelope in C5 format should have a similar design.

Target Market(s)

Private customers as well as entrepreneurs

Contact Information for Business Card

E-mail: info@kelvaro-example.ch
Web.www.Kelvaro-example.ch
Tel: +41 ( 0 ) 79 482 6037
Adresse:
Lindenweg 14
9406 Tarnbach

Hier kann man Icons verwenden für Email,Tel und Adressse

Font styles to use
Other font styles liked:
• Dubai,bold

Colors

Designer to choose colors to be used in the design.

Requirements
Must have
• WOW effect
Nice to have
• R% 26 # 252; back business card with our service listings. - VEHICLE LABELING - SHOP WINDOW LABELING - STICKERS AND MUCH MORE ... in red color

```html
<!DOCTYPE html>
<html lang="en">
<head>
<meta charset="utf-8">
<title>Kelvaro.ch – Business Card</title>
<link rel="stylesheet" href="https://fonts.googleapis.com/css2?family=Quicksand:wght@400;500;700&display=swap">
<style>
  :root {
    --stage: #121212;
    --card-light: #e5e5e5;
    --card-dark: #0c0c0c;
    --band: #050505;
    --accent: #e5b81e;
    --ink: #111111;
    --muted: #6e6e6e;
    --emboss-1: #1a1a1a;
    --emboss-2: #1e1e1e;
    --emboss-3: #222222;
    --emboss-4: #272727;
    --emboss-5: #2c2c2c;
    --emboss-6: #323232;
    --emboss-7: #373737;
    --emboss-8: #3b3b3b;
    --emboss-9: #3f3f3f;
    --emboss-10: #424242;
  }
  * { margin: 0; padding: 0; box-sizing: border-box; }
  html, body { width: 1200px; height: 1200px; overflow: hidden; background: var(--stage); }
  body { position: relative; font-family: "Quicksand", sans-serif; }

  .card { position: absolute; left: 227px; width: 746px; height: 426px; }
  .card-front { top: 135px; background: var(--card-light); overflow: hidden; }
  .card-back { top: 638px; background: var(--card-dark); overflow: hidden; }

  .side-band { position: absolute; left: 0; top: 0; width: 57px; height: 100%; background: var(--band); }
  .accent-rule { position: absolute; left: 57px; top: 0; width: 6px; height: 100%; background: var(--accent); }

  .brand { position: absolute; left: 120px; top: 84px; display: flex; align-items: center; gap: 14px; }
  .brand-dot { width: 18px; height: 18px; border-radius: 50%; background: var(--accent); }
  .brand-name { font-size: 42px; font-weight: 700; color: var(--ink); letter-spacing: 0.5px; line-height: 1; }

  .person { position: absolute; left: 153px; top: 246px; }
  .person-name { font-size: 22px; font-weight: 700; color: var(--accent); letter-spacing: 1.5px; line-height: 1.1; }
  .person-role { font-size: 18px; font-weight: 500; color: var(--muted); letter-spacing: 1.2px; margin-top: 3px; }

  .contacts { position: absolute; left: 153px; top: 330px; list-style: none; }
  .contact { display: flex; align-items: center; gap: 11px; height: 24.5px; font-size: 16px; font-weight: 500; color: var(--muted); letter-spacing: 0.8px; white-space: nowrap; }
  .contact-icon { width: 18px; height: 18px; flex: none; }
  .contact .highlight { color: var(--accent); font-weight: 700; }

  .address { position: absolute; left: 470px; top: 356px; font-size: 18.5px; font-weight: 500; color: var(--muted); letter-spacing: 1.5px; line-height: 23px; font-style: normal; white-space: nowrap; }

  .name-grid { position: absolute; left: 0; top: 0; width: 100%; height: 100%; display: grid; grid-template-columns: repeat(10, 1fr); grid-template-rows: repeat(5, 1fr); }
  .name-tile { display: flex; align-items: center; justify-content: center; font-size: 9px; font-weight: 700; letter-spacing: 0.5px; white-space: nowrap; }
  .name-tile:nth-child(10n+1) { color: var(--emboss-1); }
  .name-tile:nth-child(10n+2) { color: var(--emboss-2); }
  .name-tile:nth-child(10n+3) { color: var(--emboss-3); }
  .name-tile:nth-child(10n+4) { color: var(--emboss-4); }
  .name-tile:nth-child(10n+5) { color: var(--emboss-5); }
  .name-tile:nth-child(10n+6) { color: var(--emboss-6); }
  .name-tile:nth-child(10n+7) { color: var(--emboss-7); }
  .name-tile:nth-child(10n+8) { color: var(--emboss-8); }
  .name-tile:nth-child(10n+9) { color: var(--emboss-9); }
  .name-tile:nth-child(10n) { color: var(--emboss-10); }
  .name-tile.is-accent { color: var(--accent); }
</style>
</head>
<body>
  <section class="card card-front">
    <div class="side-band"></div>
    <div class="accent-rule"></div>

    <div class="brand">
      <span class="brand-dot"></span>
      <span class="brand-name">KELVARO.CH</span>
    </div>

    <div class="person">
      <div class="person-name">LENA BRUNNER</div>
      <div class="person-role">Managing Director</div>
    </div>

    <ul class="contacts">
      <li class="contact">
        <svg class="contact-icon" viewBox="0 0 18 18"><circle cx="9" cy="9" r="9" fill="var(--accent)"/><path d="M4.5 7.2c0-1.6 2-2.4 4.5-2.4s4.5.8 4.5 2.4H11.6V6.4H6.4v.8z M5.8 8.2h6.4l.6 4.6H5.2z" fill="#f4f4f4"/><circle cx="9" cy="10.5" r="1.2" fill="var(--accent)"/></svg>
        <span>+41 ( 0 ) 79 482 6037</span>
      </li>
      <li class="contact">
        <svg class="contact-icon" viewBox="0 0 18 18"><circle cx="9" cy="9" r="9" fill="var(--accent)"/><rect x="4.3" y="5.8" width="9.4" height="6.4" fill="none" stroke="#f4f4f4" stroke-width="1.1"/><path d="M4.3 5.8 9 9.6l4.7-3.8" fill="none" stroke="#f4f4f4" stroke-width="1.1"/></svg>
        <span>info@kelvaro-example.ch</span>
      </li>
      <li class="contact">
        <svg class="contact-icon" viewBox="0 0 18 18"><circle cx="9" cy="9" r="9" fill="var(--accent)"/><circle cx="9" cy="9" r="5.2" fill="none" stroke="#f4f4f4" stroke-width="1.1"/><path d="M5.6 7.2c1.2.4 1.8 1.4 1.3 2.6.9.6.8 1.6.4 2.4M10.6 4.3c-.3 1.3.6 1.7 1.6 1.9.3 1 1 1.3 1.7 1.2" fill="none" stroke="#f4f4f4" stroke-width="1.1"/></svg>
        <span>www.<span class="highlight">Kelvaro-example</span>.ch</span>
      </li>
    </ul>

    <address class="address">Lindenweg 14<br>9406 Tarnbach</address>
  </section>

  <section class="card card-back">
    <div class="name-grid">
      <span class="name-tile">KELVARO.CH</span><span class="name-tile">KELVARO.CH</span><span class="name-tile">KELVARO.CH</span><span class="name-tile">KELVARO.CH</span><span class="name-tile">KELVARO.CH</span><span class="name-tile">KELVARO.CH</span><span class="name-tile">KELVARO.CH</span><span class="name-tile">KELVARO.CH</span><span class="name-tile">KELVARO.CH</span><span class="name-tile">KELVARO.CH</span>
      <span class="name-tile">KELVARO.CH</span><span class="name-tile">KELVARO.CH</span><span class="name-tile">KELVARO.CH</span><span class="name-tile">KELVARO.CH</span><span class="name-tile">KELVARO.CH</span><span class="name-tile">KELVARO.CH</span><span class="name-tile">KELVARO.CH</span><span class="name-tile">KELVARO.CH</span><span class="name-tile">KELVARO.CH</span><span class="name-tile">KELVARO.CH</span>
      <span class="name-tile">KELVARO.CH</span><span class="name-tile">KELVARO.CH</span><span class="name-tile">KELVARO.CH</span><span class="name-tile">KELVARO.CH</span><span class="name-tile">KELVARO.CH</span><span class="name-tile">KELVARO.CH</span><span class="name-tile">KELVARO.CH</span><span class="name-tile">KELVARO.CH</span><span class="name-tile">KELVARO.CH</span><span class="name-tile">KELVARO.CH</span>
      <span class="name-tile">KELVARO.CH</span><span class="name-tile">KELVARO.CH</span><span class="name-tile">KELVARO.CH</span><span class="name-tile">KELVARO.CH</span><span class="name-tile">KELVARO.CH</span><span class="name-tile">KELVARO.CH</span><span class="name-tile">KELVARO.CH</span><span class="name-tile">KELVARO.CH</span><span class="name-tile is-accent">KELVARO.CH</span><span class="name-tile">KELVARO.CH</span>
      <span class="name-tile">KELVARO.CH</span><span class="name-tile">KELVARO.CH</span><span class="name-tile">KELVARO.CH</span><span class="name-tile">KELVARO.CH</span><span class="name-tile">KELVARO.CH</span><span class="name-tile">KELVARO.CH</span><span class="name-tile">KELVARO.CH</span><span class="name-tile">KELVARO.CH</span><span class="name-tile">KELVARO.CH</span><span class="name-tile">KELVARO.CH</span>
    </div>
  </section>
</body>
</html>
```